Website for "Bright Morrow Ltd" cleaning bsuiness

We require a website to expose our business to the local market. We want to provide background on who we are and what we do but in an easily digestible way. We clean domestic and commercial premises and want to provide a list of all of our services to potential customers. We operate out of Warrington in the UK.

We would like the website to be animated in some way so that the experience of using it is not dull or mundane. This website needs to be an extension of our company.

Target Market(s)

30 - 60 year olds for Domestic plus commercial clients

Industry/Entity Type

Cleaning Service

Coding

Coded - Design and coding required

Number of Pages Required

4 page

Font styles to use
Sans Serif

Colors
0455a3
3176b5
85acd3
cfdeed
ffffff
000000
1b1b1b
c8c8c8
757575

Requirements
Must have
• Logo which has been provided. Theme based around the logo and its colours. Simple layout to avoid confusion.
Nice to have
• Animations where possible to impress the customer.
Should not have
• any pictures of cleaning equipment, fairies, maids etc

```html
<!DOCTYPE html>
<html lang="en">
<head>
<meta charset="utf-8">
<title>Bright Morrow Ltd – Professional Cleaning Service</title>
<link href="https://fonts.googleapis.com/css2?family=Open+Sans:ital,wght@0,400;0,600;0,700;0,800;1,400&display=swap" rel="stylesheet">
<style>
:root{
  --brand:#0455a3;
  --brand-mid:#3176b5;
  --brand-soft:#85acd3;
  --brand-pale:#cfdeed;
  --white:#ffffff;
  --black:#000000;
  --ink:#1b1b1b;
  --line:#c8c8c8;
  --muted:#757575;
  --text:#555555;
  --dark-btn:#3a3a3a;
}
*{box-sizing:border-box;margin:0;padding:0}
html,body{width:1200px;height:3358px;overflow:hidden}
body{font-family:'Open Sans',Arial,sans-serif;color:var(--text);background:var(--white);position:relative}
.abs{position:absolute}
.center{text-align:center}

/* header */
.site-header{position:absolute;left:0;top:0;width:1200px;height:138px;background:var(--white);border-top:4px solid var(--brand-soft)}
.contact-tab{position:absolute;left:712px;top:0;width:412px;height:44px;background:var(--brand-mid);color:var(--white);font-size:14px;display:flex;align-items:center;justify-content:center;gap:14px;clip-path:polygon(0 0,100% 0,97% 100%,3% 100%)}
.contact-tab span{display:flex;align-items:center;gap:8px}
.logo{position:absolute;left:75px;top:30px;display:flex;align-items:center;gap:12px;color:var(--brand);font-weight:800;font-size:30px;line-height:1}
.logo-dot{width:52px;height:52px;border-radius:50%;background:var(--brand)}
.main-nav{position:absolute;right:75px;top:88px;display:flex;gap:0;font-size:13px;font-weight:700;color:var(--ink)}
.main-nav a{color:inherit;text-decoration:none;padding:9px 20px;letter-spacing:.3px}
.main-nav a.active{background:var(--brand);color:var(--white)}

/* hero */
.hero{position:absolute;left:0;top:138px;width:1200px;height:540px;background:linear-gradient(180deg,#1c2c45 0%,#34507a 30%,#4d6a92 55%,#223550 80%,#141f30 100%)}
.hero h1{position:absolute;top:145px;width:100%;text-align:center;color:var(--white);font-size:72px;font-weight:800;letter-spacing:1px}
.hero h2{position:absolute;top:225px;width:100%;text-align:center;color:var(--white);font-size:31px;font-weight:700}
.btn{position:absolute;display:flex;align-items:center;justify-content:center;font-size:14px;font-weight:700;color:var(--white);letter-spacing:.4px;text-transform:uppercase}
.btn-blue{background:var(--brand)}
.btn-dark{background:linear-gradient(#4a4a4a,#2a2a2a)}
.dots{position:absolute;display:flex;gap:8px}
.dots i{width:10px;height:10px;border-radius:50%;background:var(--white);display:block}
.dots i.off{background:transparent;border:2px solid var(--white)}

/* sections */
.section-title{position:absolute;width:100%;text-align:center;font-size:27px;font-weight:700;color:var(--ink);letter-spacing:.5px}
.lead{position:absolute;left:100px;width:1000px;text-align:center;font-size:15px;line-height:26px;color:var(--muted)}
.photo{position:absolute}
.col-text{position:absolute;width:512px;text-align:center;font-size:15px;line-height:25px;color:var(--muted)}

.services{position:absolute;left:0;top:1295px;width:1200px;height:722px;background:linear-gradient(180deg,var(--brand-pale) 0%,#eef3f9 45%,var(--white) 100%)}
.service-card{position:absolute;top:185px;width:330px;height:388px;background:var(--brand);color:var(--white);text-align:center}
.service-card .photo{left:0;top:0;width:330px;height:175px}
.service-card .wave{position:absolute;left:0;top:140px}
.service-icon{position:absolute;left:123px;top:165px;width:84px;height:84px;border-radius:50%;background:var(--brand);border:4px solid var(--white);display:flex;align-items:center;justify-content:center}
.service-card h3{position:absolute;top:277px;width:100%;font-size:18px;font-weight:700;letter-spacing:.3px}
.service-card p{position:absolute;top:307px;width:100%;font-size:15px;line-height:24px}

.why{position:absolute;left:0;top:2017px;width:1200px;height:453px;background:linear-gradient(180deg,#3b3b3b 0%,#262626 55%,#1a1a1a 100%)}
.why .section-title,.why .lead{color:var(--white)}
.feature{position:absolute;top:150px;width:330px;text-align:center;color:var(--white)}
.feature h4{margin-top:18px;font-size:18px;font-weight:600}
.feature p{margin-top:6px;font-size:15px;line-height:24px}

.testimonials{position:absolute;left:0;top:2470px;width:1200px;height:585px;background:linear-gradient(180deg,var(--white) 0%,#f2f3f5 28%,#a8b3c0 55%,#4e5d70 100%)}
.quote{position:absolute;top:180px;width:330px;height:166px;background:var(--white);padding:18px 22px;font-size:15px;line-height:24px;font-style:italic;color:var(--muted);box-shadow:0 2px 6px rgba(0,0,0,.12)}
.ribbon{position:absolute;top:350px;width:160px;height:40px;background:var(--brand);color:var(--white);font-size:14px;font-weight:700;display:flex;align-items:center;justify-content:center;clip-path:polygon(0 0,100% 0,88% 100%,0 100%)}
.avatar{position:absolute;top:320px;width:100px;height:100px;border-radius:50%;background:linear-gradient(180deg,#d8dde3,#9aa6b3);border:4px solid var(--white)}

.site-footer{position:absolute;left:0;top:3055px;width:1200px;height:303px;background:var(--ink);color:#d0d0d0;font-size:13px}
.footer-logo{position:absolute;left:75px;top:62px;display:flex;align-items:center;gap:10px;color:#e2e2e2;font-weight:800;font-size:24px}
.footer-logo .logo-dot{width:40px;height:40px;background:#e2e2e2}
.footer-col{position:absolute;top:52px}
.footer-col h5{font-size:14px;font-weight:700;color:var(--white);letter-spacing:.5px;margin-bottom:14px}
.footer-col li{list-style:none;line-height:26px}
.social{position:absolute;left:75px;top:232px;display:flex;gap:16px}
.social i{display:block;width:20px;height:20px;background:#e2e2e2;border-radius:3px}
.contact-line{display:flex;align-items:center;gap:8px}
</style>
</head>
<body>

<header class="site-header">
  <div class="contact-tab">
    <span><svg width="13" height="13" viewBox="0 0 24 24"><path fill="#fff" d="M6.6 10.8a15 15 0 0 0 6.6 6.6l2.2-2.2a1 1 0 0 1 1-.25 11.4 11.4 0 0 0 3.6.57 1 1 0 0 1 1 1V20a1 1 0 0 1-1 1A17 17 0 0 1 3 4a1 1 0 0 1 1-1h3.5a1 1 0 0 1 1 1c0 1.25.2 2.45.57 3.57a1 1 0 0 1-.25 1z"/></svg>1-800-555-0147</span>
    <span>|</span>
    <span><svg width="14" height="11" viewBox="0 0 24 18"><path fill="#fff" d="M0 0h24v18H0z"/><path fill="none" stroke="#3176b5" stroke-width="2" d="M1 1l11 9 11-9"/></svg>hello@brightmorrow.co.uk</span>
  </div>
  <div class="logo"><span class="logo-dot"></span>Bright Morrow Ltd</div>
  <nav class="main-nav">
    <a class="active">HOME</a><a>WHO WE ARE</a><a>WHAT WE DO</a><a>BLOG</a><a>REVIEWS</a><a>CAREERS</a><a>CONTACT US</a>
  </nav>
</header>

<section class="hero" role="img" aria-label="Aerial night view of a city with a river and lit bridge">
  <h1>Bright Morrow</h1>
  <h2>Professional Cleaning Service in Warrington, UK</h2>
  <div class="btn btn-blue" style="left:450px;top:296px;width:300px;height:48px">Schedule an Appointment</div>
  <div class="dots" style="left:564px;top:492px"><i></i><i></i><i></i><i></i></div>
</section>

<section class="about">
  <h2 class="section-title" style="top:725px;left:-270px">WHO WE ARE</h2>
  <h2 class="section-title" style="top:725px;left:270px">WHAT WE DO</h2>
  <div class="photo" role="img" aria-label="Bright open-plan living room with sofa and large windows" style="left:75px;top:778px;width:512px;height:264px;background:linear-gradient(180deg,#d8dadb,#b7b2a8 60%,#8d8780)"></div>
  <div class="photo" role="img" aria-label="Clean modern office reception with white desk and chair" style="left:614px;top:778px;width:512px;height:264px;background:linear-gradient(180deg,#e6e8ea,#c9cdd0 55%,#a9aeb2)"></div>
  <p class="col-text" style="left:75px;top:1060px">Aliquam molestie, mi et imperdiet euismod, dui purus auctor tellus, et interdum lacus lectus et ante. Sed accumsan sollicitudin sapien, sit amet adipiscing turpis gravida ac. In congue, neque ac lobortis volutpat, libero mauris varius mi..</p>
  <p class="col-text" style="left:614px;top:1060px">Aliquam molestie, mi et imperdiet euismod, dui purus auctor tellus, et interdum lacus lectus et ante. Sed accumsan sollicitudin sapien, sit amet adipiscing turpis gravida ac. In congue, neque ac lobortis volutpat, libero mauris varius mi..</p>
  <div class="btn btn-blue" style="left:255px;top:1192px;width:152px;height:48px">Read More</div>
  <div class="btn btn-blue" style="left:794px;top:1192px;width:152px;height:48px">Read More</div>
</section>

<section class="services">
  <h2 class="section-title" style="top:40px">OUR SERVICES OFFERS</h2>
  <p class="lead" style="top:90px">Aliquam molestie, mi et imperdiet euismod, dui purus auctor tellus, et interdum lacus lectus et ante. Sed accumsan sollicitudin sapien, sit amet adipiscing turpis gravida ac.</p>

  <article class="service-card" style="left:75px">
    <div class="photo" role="img" aria-label="Tidy domestic dining room" style="background:linear-gradient(180deg,#ecebe8,#c7c2ba)"></div>
    <svg class="wave" width="330" height="40" viewBox="0 0 330 40"><path d="M0 40 Q165 -10 330 40Z" fill="#0455a3"/></svg>
    <div class="service-icon"><svg width="38" height="34" viewBox="0 0 38 34"><path fill="#fff" d="M19 2L2 17h5v15h9V22h6v10h9V17h5z"/></svg></div>
    <h3>DOMESTIC PREMISES</h3>
    <p>Sed accumsan sollicitudin sapien,<br>sit amet adipiscing turpis..</p>
  </article>

  <article class="service-card" style="left:435px">
    <div class="photo" role="img" aria-label="Commercial open office with desks" style="background:linear-gradient(180deg,#f1f1ef,#c5cfd6)"></div>
    <svg class="wave" width="330" height="40" viewBox="0 0 330 40"><path d="M0 40 Q165 -10 330 40Z" fill="#0455a3"/></svg>
    <div class="service-icon"><svg width="28" height="38" viewBox="0 0 28 38"><rect x="2" y="2" width="24" height="34" fill="#fff"/><g fill="#0455a3"><rect x="6" y="6" width="4" height="4"/><rect x="12" y="6" width="4" height="4"/><rect x="18" y="6" width="4" height="4"/><rect x="6" y="13" width="4" height="4"/><rect x="12" y="13" width="4" height="4"/><rect x="18" y="13" width="4" height="4"/><rect x="6" y="20" width="4" height="4"/><rect x="12" y="20" width="4" height="4"/><rect x="18" y="20" width="4" height="4"/><rect x="11" y="28" width="6" height="8"/></g></svg></div>
    <h3>COMMERCIAL PREMISES</h3>
    <p>Sed accumsan sollicitudin sapien,<br>sit amet adipiscing turpis..</p>
  </article>

  <article class="service-card" style="left:795px">
    <div class="photo" role="img" aria-label="Smiling family of four" style="background:linear-gradient(180deg,#f4f5f7,#d9cbbd)"></div>
    <svg class="wave" width="330" height="40" viewBox="0 0 330 40"><path d="M0 40 Q165 -10 330 40Z" fill="#0455a3"/></svg>
    <div class="service-icon"><svg width="42" height="32" viewBox="0 0 42 32"><g fill="#fff"><circle cx="21" cy="9" r="6"/><path d="M11 30c0-7 4-11 10-11s10 4 10 11z"/><circle cx="8" cy="12" r="4.5"/><path d="M0 28c0-5 3-8 8-8 2 0 3 .5 4 1-1.5 2-2.5 4.5-2.5 7z"/><circle cx="34" cy="12" r="4.5"/><path d="M42 28c0-5-3-8-8-8-2 0-3 .5-4 1 1.5 2 2.5 4.5 2.5 7z"/></g></svg></div>
    <h3>POTENTIAL CUSTOMERS</h3>
    <p>Sed accumsan sollicitudin sapien,<br>sit amet adipiscing turpis..</p>
  </article>

  <div class="btn btn-dark" style="left:450px;top:625px;width:300px;height:48px">Schedule an Appointment</div>
</section>

<section class="why" role="img" aria-label="Dim modern living room interior in the background">
  <h2 class="section-title" style="top:40px">WHY CHOOSE US?</h2>
  <p class="lead" style="top:92px">Aliquam molestie, mi et imperdiet euismod, dui purus auctor tellus, et interdum lacus lectus et ante.</p>
  <div class="feature" style="left:75px">
    <svg width="50" height="50" viewBox="0 0 50 50"><circle cx="25" cy="25" r="21" fill="none" stroke="#fff" stroke-width="5"/><path d="M25 13v13h9" fill="none" stroke="#fff" stroke-width="4"/></svg>
    <h4>Saves Your Time</h4>
    <p>Aliquam molestie, mi et imperdiet<br>euismod, dui purus auctor.</p>
  </div>
  <div class="feature" style="left:435px">
    <svg width="52" height="50" viewBox="0 0 52 50"><g fill="#fff"><rect x="2" y="20" width="10" height="28"/><path d="M16 22 27 4c3-2 7 0 6 5l-3 10h16c3 0 5 3 4 6l-5 20c-1 2-3 3-5 3H16z"/></g></svg>
    <h4>Best Quality</h4>
    <p>Aliquam molestie, mi et imperdiet<br>euismod, dui purus auctor.</p>
  </div>
  <div class="feature" style="left:795px">
    <svg width="58" height="48" viewBox="0 0 58 48"><g fill="#fff"><ellipse cx="24" cy="17" rx="22" ry="15"/><path d="M8 26 4 40l14-8z"/><ellipse cx="40" cy="30" rx="16" ry="11" fill="#2a2a2a"/><ellipse cx="40" cy="30" rx="14" ry="9.5"/><path d="M50 35l5 10-12-6z"/></g></svg>
    <h4>Easy To Get Help</h4>
    <p>Aliquam molestie, mi et imperdiet<br>euismod, dui purus auctor.</p>
  </div>
  <div class="dots" style="left:583px;top:388px"><i class="off"></i><i></i></div>
</section>

<section class="testimonials" role="img" aria-label="Faded aerial view of a city skyline behind the testimonials">
  <h2 class="section-title" style="top:40px">OUR HAPPY CUSTOMERS</h2>
  <p class="lead" style="top:90px">Aliquam molestie, mi et imperdiet euismod, dui purus auctor tellus, et interdum lacus lectus et ante. Sed accumsan sollicitudin sapien, sit amet adipiscing turpis gravida ac.</p>

  <blockquote class="quote" style="left:75px">“ Sed accumsan sollicitudin sapien, sit amet adipiscing turpis gravida ac. In congue, neque ac lobortis volutpat, libero mauris varius mi..”</blockquote>
  <div class="ribbon" style="left:170px">DANIEL</div>
  <div class="avatar" role="img" aria-label="Customer portrait" style="left:88px"></div>

  <blockquote class="quote" style="left:435px">“ Sed accumsan sollicitudin sapien, sit amet adipiscing turpis gravida ac. In congue, neque ac lobortis volutpat, libero mauris varius mi..”</blockquote>
  <div class="ribbon" style="left:530px">DANIEL</div>
  <div class="avatar" role="img" aria-label="Customer portrait" style="left:448px"></div>

  <blockquote class="quote" style="left:795px">“ Sed accumsan sollicitudin sapien, sit amet adipiscing turpis gravida ac. In congue, neque ac lobortis volutpat, libero mauris varius mi..”</blockquote>
  <div class="ribbon" style="left:890px">DANIEL</div>
  <div class="avatar" role="img" aria-label="Customer portrait" style="left:808px"></div>

  <div class="btn btn-dark" style="left:450px;top:485px;width:300px;height:48px">Read All Testimonials</div>
</section>

<footer class="site-footer">
  <div class="footer-logo"><span class="logo-dot"></span>Bright Morrow Ltd</div>
  <p class="abs" style="left:75px;top:175px;line-height:20px;font-size:12px">Copyright © 2016, Company Name<br>All Right Reserved</p>
  <div class="social"><i></i><i></i><i></i><i></i><i></i></div>

  <div class="footer-col" style="left:380px">
    <h5>QUICK LINKS</h5>
    <ul><li>Home</li><li>Who We Are</li><li>What We Do</li><li>Blog</li><li>Reviews</li><li>Careers</li><li>Contact Us</li></ul>
  </div>
  <div class="footer-col" style="left:615px">
    <h5>SUPPORT</h5>
    <ul><li>Duis aliquam nibh</li><li>Dui iaculis viverra id a velit</li><li>Vivamus egestas</li><li>Vestibulum ante</li></ul>
  </div>
  <div class="footer-col" style="left:878px">
    <h5>CONTACT INFO</h5>
    <p style="font-weight:700;color:#fff;line-height:22px">COMPANY NAME</p>
    <p style="line-height:20px">14 Larkfield Road,<br>Warrington, WA1 4QT</p>
    <p class="contact-line" style="margin-top:8px"><svg width="12" height="12" viewBox="0 0 24 24"><path fill="#d0d0d0" d="M6.6 10.8a15 15 0 0 0 6.6 6.6l2.2-2.2a1 1 0 0 1 1-.25 11.4 11.4 0 0 0 3.6.57 1 1 0 0 1 1 1V20a1 1 0 0 1-1 1A17 17 0 0 1 3 4a1 1 0 0 1 1-1h3.5a1 1 0 0 1 1 1c0 1.25.2 2.45.57 3.57a1 1 0 0 1-.25 1z"/></svg>1-800-555-0147</p>
    <p class="contact-line" style="margin-top:8px"><svg width="13" height="10" viewBox="0 0 24 18"><path fill="#d0d0d0" d="M0 0h24v18H0z"/><path fill="none" stroke="#1b1b1b" stroke-width="2" d="M1 1l11 9 11-9"/></svg>hello@brightmorrow.co.uk</p>
  </div>
</footer>

</body>
</html>
```